AMAZING WEBSITE DESIGN NEEDED FOR MAID / CLEANING SERVICE

NOTE: This is Website Design Only - No coding required

Please submit your designs ASAP as we want to pick a winner and get started!

Hey,

We are looking for a new amazing website design for a maid or cleaning service.

They have a horrible website that we want turned into a masterpiece.

As you will see on their current site:

http://brightnookservices.example-host.net/

They have a lot of stuff, very disorganized, and need help.

Here is what we need:

Colors: Same as current site, Orange, Gray, Black

Menu: Horizontal with same Menu items

Need a spot for a video on the homepage

Want content to be structured in a great format that is easy to read.

Want to highlight commercial and residential on the website homepage.

Also want a spot for customer testimonials

We want the site clean, professional, fresh and modern.

Please help by matching the logo design.

I look forward to your designs!
Updates

Hi All! Really appreciate your efforts and designs. I will be meeting with our client on Monday and will then be able to provide feedback after our meeting. If you have other ideas, please submit them. The more I can show him the better! Thanks!

Target Market(s)

The target market is residential home owners as well as commercial businesses who need cleaning on a regular basis.

This company cleans homes and offices for individuals.

Industry/Entity Type

Residential

Font styles to use
Sans Serif

Requirements
Must have
• Must match logo colors
Must have spot for video
Must have a clean look
Must have a bold look
Nice to have
• Highly visual
Should not have
• clutter
messy design
hard to read

```html
<!DOCTYPE html>
<html lang="en">
<head>
<meta charset="utf-8">
<title>Bright Nook – Home</title>
<link href="https://fonts.googleapis.com/css2?family=Open+Sans:wght@400;600&family=Oswald:wght@400&family=Lobster&display=swap" rel="stylesheet">
<style>
:root{
  --orange:#ff8a00;
  --orange-deep:#f57a00;
  --page:#ebeced;
  --panel:#f3f4f5;
  --border:#cfd1d3;
  --text:#555;
  --dark:#222;
  --red:#d8261c;
  --green:#3d8b2f;
}
*{margin:0;padding:0;box-sizing:border-box}
html,body{width:873px;height:1200px;overflow:hidden}
body{background:var(--page);font-family:"Open Sans",sans-serif;color:var(--text);position:relative}
.abs{position:absolute}
.top-bar{left:0;top:0;width:873px;height:6px;background:var(--orange)}
.top-tab{left:664px;top:0;width:136px;height:30px;background:var(--orange);border-radius:0 0 18px 18px;color:#fff;font-size:9.5px;text-align:center;line-height:30px}
.brand{left:72px;top:26px;display:flex;align-items:center;gap:8px}
.brand-mark{width:26px;height:26px;background:var(--orange)}
.brand-name{font-size:22px;font-weight:600;color:var(--dark);line-height:1}
.brand-tag{left:98px;top:62px;font-size:7px;color:#666;font-style:italic}
.contact-line{right:73px;font-size:10.5px;color:var(--dark);text-align:right}
.contact-line span{color:var(--orange)}
.band{left:0;top:172px;width:873px;height:194px;background:var(--orange)}
.panel{left:72px;top:94px;width:728px;height:1018px;background:var(--panel);border:1px solid var(--border)}
.nav{left:73px;top:95px;width:726px;height:38px;border-bottom:1px solid var(--border);display:flex;align-items:center;padding-left:21px}
.nav a{font-size:10.5px;color:#555;text-decoration:none;padding:0 9px;border-right:1px solid #ddd;line-height:22px}
.nav a:last-child{border-right:none}
.nav a.active{color:var(--orange);padding-left:0}
.slider{left:94px;top:140px;width:684px;height:253px;border-radius:6px;background:linear-gradient(135deg,#8a8a82 0%,#d9d9d4 45%,#b9b4a8 70%,#4e4a44 100%);overflow:hidden}
.slider-title{left:166px;top:224px;font-family:"Oswald",sans-serif;font-size:22px;color:#fff;line-height:35px;text-shadow:0 1px 3px rgba(0,0,0,.5)}
.arrow{width:22px;height:22px;border-radius:50%;background:#fff;box-shadow:0 1px 3px rgba(0,0,0,.4)}
.dot{width:9px;height:9px;border-radius:50%;border:1.5px solid #fff;top:378px}
.h2{font-size:24px;color:var(--orange);font-weight:400}
.body-text{font-size:8.8px;line-height:16px;color:#555}
.more{font-size:9.5px;color:var(--orange)}
.video{left:554px;top:414px;width:224px;height:148px;border-radius:8px;background:linear-gradient(160deg,#6a4a2a,#c9904f 50%,#5a3a1e);border:1px solid #bbb}
.photo{width:213px;height:139px;top:645px}
.photo.commercial{left:94px;background:linear-gradient(180deg,#4d8ed8 0%,#9cc3ea 45%,#9aa3aa 75%,#4b5a36 100%)}
.photo.residential{left:330px;background:linear-gradient(180deg,#3f79c4 0%,#b9d1ea 40%,#e2e2e0 65%,#4f8a2d 100%)}
.photo.offers{left:564px;background:linear-gradient(160deg,#6d5a45,#a48b6c 50%,#4d3c2d)}
.offers-title{left:564px;top:677px;width:213px;text-align:center;font-family:"Lobster",cursive;font-size:24px;color:var(--orange)}
.btn{background:var(--orange);color:#fff;font-size:9.5px;text-align:center;border-radius:2px}
.h3{font-size:13px;color:var(--dark)}
.label{font-size:9px;color:var(--orange)}
.value{font-size:9px;color:#555}
.finder{left:564px;top:799px;width:213px;height:117px;background:linear-gradient(180deg,#ffa31a,#ff7a00);color:#fff;padding:10px}
.finder h4{font-size:10.5px;font-weight:400}
.finder p{font-size:8.2px;font-weight:600;line-height:13px;margin-top:4px}
.zip-input{left:625px;top:860px;width:139px;height:22px;background:#fff;border:1px solid #ddd}
.send{left:723px;top:889px;width:37px;height:18px;background:var(--green);color:#fff;font-size:9px;text-align:center;line-height:18px;border-radius:2px}
.avatar{width:66px;height:66px;border-radius:50%;background:radial-gradient(circle,#8c7a6a,#c8c8c8 70%);border:3px solid #bbb}
.quote-title{font-size:8.6px;color:var(--red)}
.quote{font-size:8.8px;line-height:13px;color:#444;width:135px}
.footer-nav{left:71px;top:1130px;font-size:13px;color:#555}
.footer-nav span{color:#888;padding:0 6px}
.copy{left:71px;top:1156px;font-size:9px;color:#777}
.social{width:18px;height:18px;top:1133px;border-radius:2px}
</style>
</head>
<body>
<div class="abs top-bar"></div>
<div class="abs top-tab">About Us \ Contact Us</div>

<div class="abs brand"><div class="brand-mark"></div><div class="brand-name">Bright Nook</div></div>
<div class="abs brand-tag">Quality Commercial &amp; Residential Cleaning</div>
<div class="abs contact-line" style="top:48px"><span>Phone:</span> +42 555-19-07</div>
<div class="abs contact-line" style="top:66px"><span>E-Mail:</span> hello@brightnook.example</div>

<div class="abs band"></div>
<div class="abs panel"></div>

<nav class="abs nav">
  <a class="active">Home</a><a>Our Services</a><a>Our Employees</a><a>Why Choose</a><a>Bright Nook?</a><a>Testimonlials</a><a>Special Offers</a><a>Meet the President &amp; CEO</a>
</nav>

<div class="abs slider" role="img" aria-label="Bright, spotless modern living room with white sectional sofa"></div>
<div class="abs slider-title">Wouldn’t it be nice,<br>To come home to a perfectly clean house?</div>
<div class="abs arrow" style="left:115px;top:249px"><svg width="22" height="22"><path d="M13 6l-5 5 5 5" stroke="#333" stroke-width="2" fill="none"/></svg></div>
<div class="abs arrow" style="left:727px;top:249px"><svg width="22" height="22"><path d="M9 6l5 5-5 5" stroke="#333" stroke-width="2" fill="none"/></svg></div>
<div class="abs dot" style="left:401px;background:var(--orange);border-color:var(--orange)"></div>
<div class="abs dot" style="left:415px"></div>
<div class="abs dot" style="left:431px"></div>

<h2 class="abs h2" style="left:94px;top:416px">Welcome to our website!!</h2>
<p class="abs body-text" style="left:94px;top:449px;width:442px">Thank you for visiting us! You are one step closer to experiencing first class maid service! Our company specializes in detailed housekeeping, janitorial, and commerical cleaning services making your environment shine and sparkle like it never has before!  Our maids are fully trained professionals who we recruit from high end luxury hotels we know, like the Grand Harbor and Stellaris! We pride ourselves in delivering exceptional service to our valued customers by fully understanding what your expectations &amp; needs are! We will strive for perfection and we will provide an uncompromising</p>
<div class="abs more" style="left:94px;top:548px">Read More +</div>

<div class="abs video" role="img" aria-label="Video thumbnail of a clean kitchen"></div>
<svg class="abs" style="left:645px;top:467px" width="42" height="42"><circle cx="21" cy="21" r="21" fill="#e8453c" opacity=".9"/><path d="M16 11l14 10-14 10z" fill="#fff"/></svg>

<h2 class="abs h2" style="left:94px;top:597px">Our Services</h2>

<div class="abs photo commercial" role="img" aria-label="Modern glass office building"></div>
<div class="abs photo residential" role="img" aria-label="White family house with lawn"></div>
<div class="abs photo offers" role="img" aria-label="Cosy living room interior"></div>
<div class="abs offers-title">Specail offers</div>
<div class="abs btn" style="left:626px;top:722px;width:90px;height:26px;line-height:26px">CLICK HERE</div>

<h3 class="abs h3" style="left:94px;top:793px;font-weight:400">Commercial</h3>
<p class="abs body-text" style="left:94px;top:816px;width:212px;line-height:16.6px">Lorem ipsum dolor sit amet, consectetuer adipiscing elit, sed diam nonummy nibh euismod tincidunt ut laoreet dolore magna aliquam erat volutpat. Lorem ipsum dolor sit amet, consectetuer adipiscing elit, sed diam nonummy .</p>
<div class="abs more" style="left:94px;top:903px">Read More +</div>

<h3 class="abs h3" style="left:331px;top:793px;font-weight:400">Residential</h3>
<div class="abs label" style="left:331px;top:818px">Type :</div><div class="abs value" style="left:385px;top:818px">Master Planned Single Family</div>
<div class="abs label" style="left:331px;top:841px">Size :</div><div class="abs value" style="left:385px;top:841px">600 units at build-out</div>
<div class="abs label" style="left:331px;top:864px">Amenities:</div><div class="abs value" style="left:383px;top:864px;line-height:16px;width:150px">State-of-the-art community with swim center and shady parks.</div>
<div class="abs more" style="left:332px;top:903px">Read More +</div>

<div class="abs finder"><h4>Find  a Bright Nook Office</h4><p>Find a BrightNook office nearest you by entering your zip code below</p></div>
<div class="abs" style="left:575px;top:864px;font-size:10.5px;color:#fff">Zip Code :</div>
<div class="abs zip-input"></div>
<div class="abs send">Send</div>

<div class="abs" style="left:95px;top:964px;font-size:13px;color:var(--orange)">What Our Clients Say</div>
<div class="abs" style="left:236px;top:976px;width:266px;height:1px;background:#bbb"></div>
<div class="abs" style="left:510px;top:972px;width:8px;height:8px;border-radius:50%;background:var(--orange)"></div>
<div class="abs" style="left:522px;top:972px;width:8px;height:8px;border-radius:50%;border:1px solid #555"></div>
<div class="abs" style="left:534px;top:972px;width:8px;height:8px;border-radius:50%;border:1px solid #555"></div>

<div class="abs avatar" style="left:94px;top:1003px" role="img" aria-label="Client portrait"></div>
<div class="abs quote-title" style="left:173px;top:1003px">Lorem ipsum dolor sit amet</div>
<p class="abs quote" style="left:173px;top:1018px">Lorem ipsum dolor sit amet, consetetur sadipscing elitr, sed diam nonumy eirmod tempor invidunt</p>
<div class="abs avatar" style="left:327px;top:1000px" role="img" aria-label="Client portrait"></div>
<div class="abs quote-title" style="left:408px;top:1003px">Lorem ipsum dolor sit amet</div>
<p class="abs quote" style="left:408px;top:1018px">Lorem ipsum dolor sit amet, consetetur sadipscing elitr, sed diam nonumy eirmod tempor invidunt</p>

<div class="abs" style="left:564px;top:966px;font-size:18px;color:var(--dark)">Quick Contact</div>
<p class="abs" style="left:566px;top:997px;width:210px;font-size:8.8px;line-height:14.5px;color:#888">Nunc tempus felis vitae urna Vivamus porttitor g purus nisi eleifend libero a tempus libero lectus</p>
<div class="abs btn" style="left:564px;top:1031px;width:90px;height:27px;line-height:27px">CLICK HERE</div>

<div class="abs footer-nav">Home<span>|</span>Our Services<span>|</span>About us<span>|</span>Our Employees<span>|</span>Contact Us<span>|</span>Blog</div>
<div class="abs copy">© 2014 Company Name  All right reserved  Term of Use</div>

<div class="abs social" style="left:712px;background:#3b5998"></div>
<div class="abs social" style="left:736px;background:#4fb8e8"></div>
<div class="abs social" style="left:759px;background:#1a6fa8"></div>
<div class="abs social" style="left:782px;background:#f7931e"></div>
</body>
</html>
```